Redesign of business card for Cedar Ridge Mechanical

We are looking for a new design for our business cards for Cedar Ridge Mechanical. We are a plumbing & HVAC construction company, operating on the West Coast of Canada and USA. Logo attached.
Industry/Entity Type
Construction - Plumbing & HVAC
Contact Information for Business Card
Name, address, phone numbers, email, website address
Look and feel
Each slider illustrates characteristics of the customer's brand and the style your logo design should communicate.

```html
<!DOCTYPE html>
<html lang="en">
<head>
<meta charset="utf-8">
<title>Cedar Ridge Mechanical – Business Card</title>
<link rel="stylesheet" href="https://fonts.googleapis.com/css2?family=Montserrat:wght@400;700&family=Oswald:wght@500&display=swap">
<style>
  :root{
    --stage:#e9e9e9;
    --paper:#ffffff;
    --ink:#1c1c1c;
    --band:#181818;
    --muted:#555555;
    --grey:#8a8a8a;
    --back-top:#2a2a2a;
    --back-bottom:#0e0e0e;
    --back-text:#8c8c8c;
  }
  *{box-sizing:border-box;margin:0;padding:0}
  html,body{width:1200px;height:801px;overflow:hidden;background:var(--stage)}
  .stage{position:relative;width:1200px;height:801px}
  .card{position:absolute;width:520px;height:298px;border-radius:22px;overflow:hidden;box-shadow:0 10px 28px rgba(0,0,0,.25)}
  .card--front{left:50px;top:130px;background:var(--paper);font-family:"Montserrat",sans-serif;color:var(--ink)}
  .card--back{left:630px;top:373px;background:linear-gradient(160deg,var(--back-top),var(--back-bottom))}

  .name-band{position:absolute;left:0;top:70px;width:330px;height:54px;background:var(--band);color:#fff;padding:8px 0 0 26px}
  .name-band .person{font-weight:700;font-size:17px;letter-spacing:.5px;display:block}
  .name-band .role{font-size:12px;display:block;margin-top:2px}

  .brand{position:absolute;left:340px;top:40px;width:160px;display:flex;flex-direction:column;align-items:flex-start;gap:8px}
  .brand .mark{width:44px;height:44px;background:var(--band)}
  .brand .brand-name{font-size:13px;font-weight:700;line-height:1.2;color:var(--ink)}
  .corner-tab{position:absolute;right:0;top:0;width:26px;height:22px;background:var(--grey)}

  .address{position:absolute;right:30px;top:150px;text-align:right;font-size:13px;line-height:1.35;color:var(--muted)}

  .contacts{position:absolute;left:26px;bottom:22px;list-style:none;font-size:13px;line-height:1.5;color:var(--ink)}
  .contacts li{display:flex;align-items:center;gap:8px}
  .contacts svg{width:12px;height:12px;fill:var(--ink)}

  .back-brand{position:absolute;inset:0;display:flex;align-items:center;justify-content:center;gap:14px}
  .back-brand .mark{width:30px;height:30px;background:var(--back-text)}
  .back-brand .brand-name{font-family:"Oswald",sans-serif;font-weight:500;font-size:30px;letter-spacing:2px;color:var(--back-text)}
</style>
</head>
<body>
<main class="stage">
  <section class="card card--front">
    <div class="corner-tab"></div>
    <div class="name-band">
      <span class="person">DANIEL HARPER</span>
      <span class="role">Manager</span>
    </div>
    <div class="brand">
      <div class="mark"></div>
      <span class="brand-name">CEDAR RIDGE MECHANICAL</span>
    </div>
    <p class="address">Your address, city<br>state, ZIP 0000</p>
    <ul class="contacts">
      <li><svg viewBox="0 0 24 24"><path d="M6.6 10.8a15 15 0 0 0 6.6 6.6l2.2-2.2a1 1 0 0 1 1-.25 11.4 11.4 0 0 0 3.6.57 1 1 0 0 1 1 1V20a1 1 0 0 1-1 1A17 17 0 0 1 3 4a1 1 0 0 1 1-1h3.5a1 1 0 0 1 1 1c0 1.25.2 2.45.57 3.6a1 1 0 0 1-.25 1z"/></svg>123-456-2100</li>
      <li><svg viewBox="0 0 24 24"><path d="M2 5h20v14H2zm2 2v.5l8 5 8-5V7z"/></svg>youremail@mailbox.com</li>
      <li><svg viewBox="0 0 24 24"><circle cx="12" cy="12" r="10"/></svg>www.yourwebsite.com</li>
    </ul>
  </section>

  <section class="card card--back">
    <div class="back-brand">
      <div class="mark"></div>
      <span class="brand-name">CEDAR RIDGE MECHANICAL</span>
    </div>
  </section>
</main>
</body>
</html>
```